Business card design for my company.
I would like the card's background colour to be black. You can also see our web site to get an idea of our brand. https://www.tmwhomecrafting.com.au/
- Name
- Email

```html
<!DOCTYPE html>
<html lang="en">
<head>
<meta charset="utf-8">
<title>TMW Home Crafting – Business Card</title>
<link href="https://fonts.googleapis.com/css2?family=Montserrat:wght@400;700&display=swap" rel="stylesheet">
<style>
  :root {
    --backdrop: #c5c6cb;
    --card: #212125;
    --card-pattern: #26262a;
    --green: #1a9a48;
    --white: #f2f2f4;
    --photo-tone: #4b4740;
  }
  * { margin: 0; padding: 0; box-sizing: border-box; }
  html, body {
    width: 1200px; height: 1129px; overflow: hidden;
    background: var(--backdrop);
    font-family: "Montserrat", sans-serif;
  }
  .stage { position: relative; width: 1200px; height: 1129px; }
  .card {
    position: absolute; top: 170px;
    width: 445px; height: 790px;
    background: var(--card);
    border-radius: 30px;
    overflow: hidden;
  }
  .card--front { left: 132px; }
  .card--back {
    left: 623px;
    background: linear-gradient(135deg, var(--card-pattern), var(--card));
  }
  .brand-name {
    position: absolute; left: 52px; top: 78px;
    color: var(--white);
    font-weight: 700; font-size: 38px; line-height: 1.15;
    letter-spacing: 1px; text-transform: uppercase;
  }
  .photo-strip {
    position: absolute; left: 0; top: 342px;
    width: 445px; height: 53px;
    background: var(--photo-tone);
  }
  .person-name {
    position: absolute; left: 49px; top: 440px;
    color: var(--green); font-weight: 700; font-size: 33px; letter-spacing: 0.5px;
    text-transform: uppercase;
  }
  .person-role {
    position: absolute; left: 49px; top: 487px;
    color: var(--white); font-size: 19px;
  }
  .divider {
    position: absolute; left: 49px; top: 539px;
    width: 68px; height: 3px; background: var(--green);
  }
  .contact-list { position: absolute; left: 46px; top: 590px; list-style: none; }
  .contact-item {
    display: flex; align-items: center; gap: 9px;
    color: var(--white); font-size: 20px; height: 24px;
  }
  .contact-item + .contact-item { margin-top: 8px; }
  .contact-item--address { margin-bottom: 21px; }
  .contact-icon { width: 22px; height: 22px; flex: none; }
  .back-pattern { position: absolute; inset: 0; background: var(--card-pattern); opacity: 0.6; }
  .back-brand {
    position: absolute; left: 222px; top: 400px;
    transform: translate(-50%, -50%) rotate(90deg);
    white-space: nowrap; text-align: center;
    color: var(--white); font-weight: 700; font-size: 50px; line-height: 1.1;
    letter-spacing: 2px; text-transform: uppercase;
  }
</style>
</head>
<body>
<main class="stage">
  <section class="card card--front">
    <h1 class="brand-name">TMW<br>Home Crafting</h1>

    <div class="photo-strip" role="img" aria-label="Photo of a lit modern home at dusk"></div>

    <h2 class="person-name">Liam Harcourt</h2>
    <p class="person-role">General Manager</p>
    <div class="divider"></div>

    <ul class="contact-list">
      <li class="contact-item contact-item--address">
        <svg class="contact-icon" viewBox="0 0 22 22"><circle cx="11" cy="11" r="11" fill="var(--green)"/><path d="M11 5a4 4 0 0 0-4 4c0 3 4 7.5 4 7.5s4-4.5 4-7.5a4 4 0 0 0-4-4zm0 5.6a1.6 1.6 0 1 1 0-3.2 1.6 1.6 0 0 1 0 3.2z" fill="#fff"/></svg>
        Kingsford, Tasmania, Australia
      </li>
      <li class="contact-item">
        <svg class="contact-icon" viewBox="0 0 22 22"><circle cx="11" cy="11" r="11" fill="var(--green)"/><path d="M6 8.5c0-1.5 2.2-2.5 5-2.5s5 1 5 2.5v1h-2.5V8.3h-5v1.2H6zM7.5 11l2-1.5h3l2 1.5v4h-7z" fill="#fff"/></svg>
        0400 123 456
      </li>
      <li class="contact-item">
        <svg class="contact-icon" viewBox="0 0 22 22"><circle cx="11" cy="11" r="11" fill="var(--green)"/><rect x="6" y="7.5" width="10" height="7" rx="1" fill="#fff"/><path d="M6.5 8l4.5 3.6L15.5 8" fill="none" stroke="var(--green)" stroke-width="1.2"/></svg>
        info@tmwhomecrafting.com.au
      </li>
      <li class="contact-item">
        <svg class="contact-icon" viewBox="0 0 22 22"><circle cx="11" cy="11" r="11" fill="var(--green)"/><circle cx="11" cy="11" r="5.5" fill="none" stroke="#fff" stroke-width="1.3"/><path d="M5.5 11h11M11 5.5c-2 2-2 9 0 11M11 5.5c2 2 2 9 0 11" fill="none" stroke="#fff" stroke-width="1"/></svg>
        www.tmwhomecrafting.com.au
      </li>
    </ul>
  </section>

  <section class="card card--back">
    <div class="back-pattern" role="img" aria-label="Subtle embossed chevron texture across the card"></div>
    <p class="back-brand">TMW<br>Home Crafting</p>
  </section>
</main>
</body>
</html>
```